Tandem Hearth Works Pty Ltd

We need business cards for a company based in Perth, we install, service and maintain fire equipment.
On the front we want a great design with our logo and a small spot for our full company name, general company email address and office number. On the back we need space for our name, title, mobile number and email address on the back.

Target Market(s)

Facility managers and commercial/industrial building owners/occupiers.

Contact Information for Business Card

Font styles to use
Sans Serif

Requirements
Must have
• Please only submit 5 of your best samples.
Darker tones are preferred.
Nice to have
• We want to use, black, red and grey. Keep it modern and clean.
I've attached the company logo and a sample of a boarder we use on our emergency plans.
Should not have
• No preference. Let the designer choose.

```html
<!DOCTYPE html>
<html lang="en">
<head>
<meta charset="utf-8">
<title>Tandem Hearth Works – Business Card</title>
<link href="https://fonts.googleapis.com/css2?family=Arimo:wght@400;700&display=swap" rel="stylesheet">
<style>
  :root {
    --brand-red: #ec1c24;
    --ink: #2b2b2b;
    --rule: #9a9a9a;
    --paper: #ffffff;
    --backdrop: #a8a8a8;
  }
  * { margin: 0; padding: 0; box-sizing: border-box; }
  html, body {
    width: 1200px; height: 1200px; overflow: hidden;
    background: var(--backdrop);
    font-family: "Arimo", Arial, sans-serif;
  }
  .stage { position: relative; width: 1200px; height: 1200px; }
  .card {
    position: absolute; top: 303px;
    width: 368px; height: 594px;
    background: var(--paper); overflow: hidden;
  }
  .card--front { left: 200px; }
  .card--back { left: 600px; }

  /* Front */
  .block { position: absolute; background: var(--brand-red); }
  .block--top { left: 0; top: 0; width: 190px; height: 177px; }
  .block--bottom { left: 174px; top: 416px; width: 194px; height: 178px; }
  .front-name {
    position: absolute; left: 6px; top: 206px;
    color: var(--brand-red); font-weight: 700;
    font-size: 62px; line-height: 0.96; letter-spacing: -1px;
    text-transform: uppercase;
  }

  /* Back */
  .back-name {
    position: absolute; left: 0; right: 0; top: 112px;
    text-align: center; color: var(--brand-red);
    font-weight: 700; font-size: 40px; line-height: 1.0;
    letter-spacing: -0.5px; text-transform: uppercase;
  }
  .details {
    position: absolute; left: 0; right: 0; top: 296px;
    text-align: center; color: var(--ink);
  }
  .person { color: var(--brand-red); font-weight: 700; font-size: 24px; line-height: 28px; }
  .role { font-size: 19px; line-height: 22px; }
  .rule { width: 133px; height: 1px; background: var(--rule); margin: 12px auto 10px; }
  .line { font-size: 18px; line-height: 24px; }
  .company { color: var(--brand-red); font-weight: 700; font-size: 22px; line-height: 27px; text-transform: uppercase; }
  .office { font-weight: 700; font-size: 24px; line-height: 28px; margin-top: 8px; }
  .web { font-size: 16px; line-height: 20px; margin-top: 10px; }
</style>
</head>
<body>
<main class="stage">
  <section class="card card--front">
    <div class="block block--top"></div>
    <p class="front-name">Tandem<br>Hearth<br>Works</p>
    <div class="block block--bottom"></div>
  </section>

  <section class="card card--back">
    <p class="back-name">Tandem<br>Hearth<br>Works</p>
    <div class="details">
      <p class="person">MARCUS HALE</p>
      <p class="role">Managing Director</p>
      <div class="rule"></div>
      <p class="line">789.4521.6603</p>
      <p class="line">name@tandemhearth.com</p>
      <div class="rule"></div>
      <p class="company">Tandem Hearth<br>Works Pty Ltd</p>
      <p class="office">789.3316.2048</p>
      <p class="web">info@tandemhearth.com | www.tandemhearth.com</p>
    </div>
  </section>
</main>
</body>
</html>
```